Communication and Marketing agency needs a new presentation card

We are a group of communication and marketing agencies specialized in companies that are in the logistics and industrial sector. The head agency is TELVANO Grupo and the group consists of 4 agencies: TELVANO Media, TELVANO Digital, TELVANO Research and DifundeEnPantalla. We hace 4 offices in Spain (Madrid, Barcelona, Valencia and Murcia). We are looking for a clean and attractive design that transmits our experience, brand presence in the market and knowledge to those who receive the card.It has to maintain the colors of the logo that is attached.
Target Market(s)
logistics and industrial sector
Marketing department
Contact Information for Business Card
Clean and attractive design

```html
<!DOCTYPE html>
<html lang="es">
<head>
<meta charset="utf-8">
<title>TELVANO Grupo – Tarjeta de presentación</title>
<link href="https://fonts.googleapis.com/css2?family=Montserrat:wght@400;500;600;700&display=swap" rel="stylesheet">
<style>
  :root {
    --brand-red: #c41e2e;
    --ink: #3b3b3b;
    --ink-soft: #555;
    --card: #ffffff;
    --backdrop: #9a9a9a;
    --map-tone: #d9d9d9;
  }
  * { box-sizing: border-box; margin: 0; padding: 0; }
  html, body { width: 1200px; height: 930px; overflow: hidden; }
  body {
    background: var(--backdrop);
    font-family: "Montserrat", sans-serif;
    color: var(--ink);
    position: relative;
  }
  .card {
    position: absolute;
    left: 250px;
    width: 700px;
    height: 400px;
    background: var(--card);
    border-radius: 26px;
    overflow: hidden;
  }
  .card--offices { top: 45px; }
  .card--contact { top: 485px; }

  /* Offices side */
  .offices-map {
    position: absolute;
    left: 190px; top: 40px;
    width: 320px; height: 190px;
  }
  .offices-cities {
    position: absolute;
    top: 250px; left: 0; right: 0;
    text-align: center;
    font-weight: 700;
    font-size: 17px;
    color: var(--ink);
    white-space: nowrap;
  }
  .offices-cities .sep { color: var(--brand-red); margin: 0 6px; }
  .agency-row {
    position: absolute;
    left: 40px; right: 40px; top: 318px;
    display: flex;
    justify-content: space-between;
    align-items: center;
    gap: 20px;
  }
  .agency-name {
    font-weight: 600;
    font-size: 14px;
    color: var(--ink);
    white-space: nowrap;
  }

  /* Contact side */
  .brand-name {
    position: absolute;
    left: 44px; top: 196px;
    font-weight: 600;
    font-size: 32px;
    letter-spacing: 1px;
    color: var(--brand-red);
    white-space: nowrap;
  }
  .divider {
    position: absolute;
    left: 372px; top: 60px;
    width: 2px; height: 200px;
    background: linear-gradient(var(--brand-red) 0 45%, var(--ink) 45% 100%);
  }
  .contact {
    position: absolute;
    left: 400px; top: 66px;
  }
  .contact-name {
    font-weight: 700;
    font-size: 22px;
    color: var(--brand-red);
    white-space: nowrap;
  }
  .contact-name .surname { font-weight: 400; }
  .contact-role {
    font-size: 15px;
    font-weight: 500;
    color: var(--ink);
    margin: 4px 0 14px;
  }
  .contact-list { list-style: none; }
  .contact-list li {
    display: flex;
    align-items: center;
    gap: 10px;
    font-size: 15px;
    line-height: 26px;
    color: var(--ink-soft);
    white-space: nowrap;
  }
  .contact-list svg { width: 12px; height: 12px; flex: none; }
  .contact-list .in-mark {
    width: 12px; font-size: 12px; font-weight: 700; color: var(--brand-red);
  }
  .edge-band {
    position: absolute;
    left: 0; right: 0; bottom: 0;
    height: 12px;
    background: linear-gradient(90deg, var(--ink) 0 55%, var(--brand-red) 55% 100%);
  }
</style>
</head>
<body>

<section class="card card--offices">
  <div class="offices-map" role="img" aria-label="Mapa punteado de España con marcadores en Madrid, Barcelona, Valencia y Murcia">
    <svg width="320" height="190" viewBox="0 0 320 190">
      <rect width="320" height="190" rx="14" fill="var(--map-tone)"/>
    </svg>
  </div>
  <p class="offices-cities">Madrid<span class="sep">|</span>Barcelona<span class="sep">|</span>Valencia<span class="sep">|</span>Murcia</p>
  <div class="agency-row">
    <span class="agency-name">TELVANO Digital</span>
    <span class="agency-name">DifundeEnPantalla</span>
    <span class="agency-name">TELVANO Media</span>
    <span class="agency-name">TELVANO Research</span>
  </div>
</section>

<section class="card card--contact">
  <span class="brand-name">TELVANO Grupo</span>
  <div class="divider"></div>
  <div class="contact">
    <p class="contact-name">Álvaro <span class="surname">Ribera</span></p>
    <p class="contact-role">Director</p>
    <ul class="contact-list">
      <li><svg viewBox="0 0 12 12"><path d="M2 1l2 0 1 3-1.5 1a6 6 0 0 0 3.5 3.5L8 7l3 1v2a1 1 0 0 1-1 1A9 9 0 0 1 1 2a1 1 0 0 1 1-1z" fill="var(--brand-red)"/></svg>910 555 274</li>
      <li><svg viewBox="0 0 12 12"><rect x="3" y="0.5" width="6" height="11" rx="1.2" fill="none" stroke="var(--brand-red)" stroke-width="1.4"/></svg>600 555 318</li>
      <li><svg viewBox="0 0 12 12"><rect x="0.8" y="2.5" width="10.4" height="7" fill="none" stroke="var(--brand-red)" stroke-width="1.3"/><path d="M1 3l5 4 5-4" fill="none" stroke="var(--brand-red)" stroke-width="1.3"/></svg>aribera@telvano.es</li>
      <li><svg viewBox="0 0 12 12"><circle cx="6" cy="6" r="5" fill="none" stroke="var(--brand-red)" stroke-width="1.3"/><path d="M1 6h10M6 1c2.5 3 2.5 7 0 10M6 1c-2.5 3-2.5 7 0 10" fill="none" stroke="var(--brand-red)" stroke-width="1"/></svg>www.telvano.es</li>
      <li><span class="in-mark">in</span>alvaroribera</li>
    </ul>
  </div>
  <div class="edge-band"></div>
</section>

</body>
</html>
```